Business Card Design Project - 2 sided

We need a business card design for a card having one business on each side (ie. two businesses on one card). Would like a design that incorporates logo, tagline and normal fields (name, position, address, phone).

Would also like an allowance for small font text along the bottom (text to be determined, but less than 50 characters).

NB. Attached logo for Harbor Quill has two variations - either can be used.

www.harborquill-example.com / www.velmaro-example.com

```html
<!DOCTYPE html>
<html lang="en">
<head>
<meta charset="utf-8">
<title>Harbor Quill / Velmaro – Business Card</title>
<link rel="stylesheet" href="https://fonts.googleapis.com/css2?family=Open+Sans:wght@400;600&display=swap">
<style>
  :root {
    --page-bg: #e9e6e1;
    --card-bg: #ffffff;
    --green: #7cc242;
    --green-line: #8dc63f;
    --navy: #29265f;
    --blue-top: #3d94d4;
    --blue-bottom: #1d6cb6;
    --text: #4d4d4d;
    --divider: #d6d6d6;
  }
  * { margin: 0; padding: 0; box-sizing: border-box; }
  html, body { width: 1200px; height: 487px; overflow: hidden; }
  body {
    background: var(--page-bg);
    font-family: "Open Sans", Arial, sans-serif;
    position: relative;
  }
  .card {
    position: absolute;
    top: 88px;
    width: 544px;
    height: 310px;
    background: var(--card-bg);
    overflow: hidden;
    box-shadow: 0 2px 6px rgba(0,0,0,0.18);
  }
  .card--harbor { left: 39px; }
  .card--velmaro { left: 618px; }

  .brand {
    position: absolute;
    left: 0;
    width: 312px;
    top: 118px;
    display: flex;
    flex-direction: column;
    align-items: center;
  }
  .brand__row { display: flex; align-items: center; gap: 10px; }
  .brand__dot { width: 30px; height: 30px; border-radius: 50%; background: var(--green); }
  .brand__name { font-size: 28px; font-weight: 600; letter-spacing: 0.5px; line-height: 1.1; }
  .card--harbor .brand__name { color: var(--navy); }
  .card--velmaro .brand__name { color: var(--blue-bottom); }
  .brand__tagline { margin-top: 6px; font-size: 10.5px; color: var(--text); }
  .card--velmaro .brand__tagline { font-size: 13px; letter-spacing: 0.6px; color: var(--navy); }

  .divider {
    position: absolute;
    left: 322px;
    top: 67px;
    width: 1px;
    height: 155px;
    background: var(--divider);
  }

  .details { position: absolute; left: 344px; top: 62px; }
  .details__name { font-size: 16.5px; font-weight: 600; color: var(--green); }
  .details__title { font-size: 13px; font-weight: 400; }
  .contact { list-style: none; margin-top: 12px; }
  .contact li {
    display: flex; align-items: center; gap: 5px;
    font-size: 13.5px; color: var(--text); height: 18px;
  }
  .contact svg { width: 10px; height: 10px; fill: var(--green); flex: none; }
  .details__note { margin-top: 10px; font-size: 11px; color: var(--text); line-height: 18px; letter-spacing: 0.2px; }

  .band { position: absolute; left: 0; top: 0; width: 544px; height: 310px; }
  .address {
    position: absolute; left: 48px; top: 277px;
    font-size: 13.5px; color: #ffffff;
  }
</style>
</head>
<body>
<svg width="0" height="0" style="position:absolute">
  <defs>
    <symbol id="icon-phone" viewBox="0 0 10 10"><circle cx="5" cy="5" r="4.5" fill="none" stroke="currentColor"/><path d="M3 2.5h1.2l.5 1.5-.7.6a4 4 0 0 0 1.6 1.6l.6-.7 1.5.5V7.2C5.5 7.6 2.6 5 3 2.5z"/></symbol>
    <symbol id="icon-mobile" viewBox="0 0 10 10"><rect x="2.5" y="0.5" width="5" height="9" rx="1"/><rect x="3.5" y="1.7" width="3" height="5" fill="#fff"/></symbol>
    <symbol id="icon-fax" viewBox="0 0 10 10"><path d="M1 3.5c2-2.5 6-2.5 8 0L8 5 6.5 4V3h-3v1L2 5z"/><rect x="2" y="5.5" width="6" height="3.5" rx="0.6"/></symbol>
    <symbol id="icon-mail" viewBox="0 0 10 10"><path d="M0.5 4.2 5 1l4.5 3.2V9h-9z"/><path d="M1.5 4.5 5 6.8l3.5-2.3" fill="none" stroke="#fff" stroke-width="0.8"/></symbol>
    <symbol id="icon-web" viewBox="0 0 10 10"><circle cx="5" cy="5" r="4.5"/><path d="M0.8 5h8.4M5 0.6c-2 2.5-2 6.3 0 8.8M5 0.6c2 2.5 2 6.3 0 8.8" fill="none" stroke="#fff" stroke-width="0.7"/></symbol>
  </defs>
</svg>

<section class="card card--harbor">
  <div class="brand">
    <div class="brand__row"><span class="brand__dot"></span><span class="brand__name">Harbor Quill</span></div>
    <p class="brand__tagline">Website Translation and Localisation Specialist...</p>
  </div>
  <div class="divider"></div>
  <div class="details">
    <p class="details__name">Your Name <span class="details__title">/ Title</span></p>
    <ul class="contact">
      <li><svg style="color:var(--green)"><use href="#icon-phone"/></svg>123-456-7890</li>
      <li><svg><use href="#icon-mobile"/></svg>123-456-7890</li>
      <li><svg><use href="#icon-fax"/></svg>123-456-7890</li>
      <li><svg><use href="#icon-mail"/></svg>name@website.com</li>
      <li><svg><use href="#icon-web"/></svg>www.website.com</li>
    </ul>
    <p class="details__note">xxxxxxxxxxxxxxxxxxxxxxxxxx<br>xxxxxxxxxxxxxxxxxxxxxxxxxx</p>
  </div>
  <svg class="band" viewBox="0 0 544 310" aria-hidden="true">
    <path d="M0 256 Q250 220 544 268 L544 273 Q250 228 0 263 Z" fill="var(--green-line)"/>
    <path d="M0 268 Q260 232 544 278 L544 310 L0 310 Z" fill="var(--navy)"/>
  </svg>
  <p class="address">Complex name, Street name City, State, zip code</p>
</section>

<section class="card card--velmaro">
  <div class="brand">
    <div class="brand__row"><span class="brand__dot"></span><span class="brand__name">Velmaro LLC</span></div>
    <p class="brand__tagline">Professional SEO Services</p>
  </div>
  <div class="divider"></div>
  <div class="details">
    <p class="details__name">Your Name <span class="details__title">/ Title</span></p>
    <ul class="contact">
      <li><svg style="color:var(--green)"><use href="#icon-phone"/></svg>123-456-7890</li>
      <li><svg><use href="#icon-mobile"/></svg>123-456-7890</li>
      <li><svg><use href="#icon-fax"/></svg>123-456-7890</li>
      <li><svg><use href="#icon-mail"/></svg>name@website.com</li>
      <li><svg><use href="#icon-web"/></svg>www.website.com</li>
    </ul>
    <p class="details__note">xxxxxxxxxxxxxxxxxxxxxxxxxx<br>xxxxxxxxxxxxxxxxxxxxxxxxxx</p>
  </div>
  <svg class="band" viewBox="0 0 544 310" aria-hidden="true">
    <defs>
      <linearGradient id="blue-band" x1="0" y1="0" x2="1" y2="0">
        <stop offset="0" stop-color="var(--blue-top)"/>
        <stop offset="1" stop-color="var(--blue-bottom)"/>
      </linearGradient>
    </defs>
    <path d="M0 256 Q250 220 544 268 L544 273 Q250 228 0 263 Z" fill="var(--green-line)"/>
    <path d="M0 268 Q260 232 544 278 L544 310 L0 310 Z" fill="url(#blue-band)"/>
  </svg>
  <p class="address">Complex name, Street name City, State, zip code</p>
</section>
</body>
</html>
```